Tech business card design

We need an amazing business card design for our new business 'Pexla' a marketing tech startup based in Sydney, Australia. We provide an online marketplace for businesses to search and buy advertising media, connect with service providers and learn more about marketing. We wish to communicate 'cool tech', reliability and professionalism and design based around our logo.

Target Market(s)

Business Owners

Contact Information for Business Card

Name
Position
Email Address
Website
Phone Number

Font styles to use
Other font styles liked:
• Avenir & Avenir Next

Colors

Designer to choose colors to be used in the design.

```html
<!DOCTYPE html>
<html lang="en">
<head>
<meta charset="utf-8">
<title>Pexla Business Card</title>
<link href="https://fonts.googleapis.com/css2?family=Nunito+Sans:wght@400;800&display=swap" rel="stylesheet">
<style>
  :root {
    --navy: #0b1a4a;
    --ink: #1a1f3d;
    --grey: #555a66;
    --paper: #ffffff;
    --stage: #e6e7ea;
    --white: #ffffff;
  }
  * { margin: 0; padding: 0; box-sizing: border-box; }
  html, body {
    width: 1200px; height: 716px; overflow: hidden;
    background: var(--stage);
    font-family: "Nunito Sans", sans-serif;
  }
  .canvas { position: relative; width: 1200px; height: 716px; }
  .card {
    position: absolute; top: 215px;
    width: 500px; height: 286px;
    box-shadow: 0 2px 8px rgba(0,0,0,0.15);
  }
  .card--back { left: 70px; background: var(--navy); }
  .card--front { left: 630px; background: var(--paper); }

  .wordmark {
    position: absolute;
    font-weight: 800;
    font-size: 66px;
    letter-spacing: -1px;
    line-height: 1;
  }
  .card--back .wordmark { left: 140px; top: 82px; color: var(--white); }
  .card--front .wordmark { left: 24px; top: 26px; color: var(--navy); font-size: 56px; }

  .back-web {
    position: absolute; left: 150px; top: 180px;
    font-size: 12px; color: var(--white);
  }

  .contact-block {
    position: absolute; right: 26px; bottom: 28px;
    text-align: right;
  }
  .person-name {
    font-weight: 800; font-size: 17px; letter-spacing: 0.5px;
    color: var(--ink);
  }
  .person-role {
    font-size: 13px; color: var(--grey); margin-bottom: 14px;
  }
  .contact-line {
    display: flex; justify-content: flex-end; align-items: center;
    gap: 8px; font-size: 13px; color: var(--grey); line-height: 19px;
  }
  .contact-line svg { width: 12px; height: 12px; fill: var(--ink); }
</style>
</head>
<body>
<div class="canvas">
  <div class="card card--back">
    <div class="wordmark">Pexla</div>
    <div class="back-web">www.pexlamail.com</div>
  </div>

  <div class="card card--front">
    <div class="wordmark">Pexla</div>
    <div class="contact-block">
      <div class="person-name">JONATHAN DOE</div>
      <div class="person-role">Managing Director</div>
      <div class="contact-line">000-123-4567
        <svg viewBox="0 0 12 12"><path d="M2 1h2.5l1 3-1.5 1a7 7 0 0 0 3 3l1-1.5 3 1V10a1 1 0 0 1-1 1A9 9 0 0 1 1 2a1 1 0 0 1 1-1z"/></svg>
      </div>
      <div class="contact-line">info@pexlamail.com
        <svg viewBox="0 0 12 12"><path d="M1 2.5h10v7H1z M1 2.5l5 4 5-4" fill="none" stroke="#1a1f3d" stroke-width="1.2"/></svg>
      </div>
      <div class="contact-line">www.pexlamail.com
        <svg viewBox="0 0 12 12"><g fill="none" stroke="#1a1f3d" stroke-width="1"><circle cx="6" cy="6" r="5"/><ellipse cx="6" cy="6" rx="2.2" ry="5"/><path d="M1 6h10M2 3.5h8M2 8.5h8"/></g></svg>
      </div>
    </div>
  </div>
</div>
</body>
</html>
```